Create a step-by-step donors pamphlet for VELTO church

I am looking to get a professionally design pamphlet that gives our donors easy steps to set up reoccurring donation through our give platform.

The ideal design should look professional and creative. No templates or weak AIs.

I've provided church logos and a text file which contains the content of the pamphlet we are trying to make.

Font styles to use
Sans Serif

Requirements
Must have
• Good branding

```html
<!DOCTYPE html>
<html lang="en">
<head>
<meta charset="utf-8">
<title>VELTO Church – Recurring Donor Pamphlet</title>
<link rel="stylesheet" href="https://fonts.googleapis.com/css2?family=Montserrat:wght@400;500;600;700;800;900&display=swap">
<style>
:root{
  --stage:#d6d6d6;
  --ink:#111111;
  --black:#0b0b0b;
  --paper:#ffffff;
  --paper-shade:#f2f2f2;
  --orange:#e8661c;
  --orange-deep:#c9470e;
  --flame-hot:#ffb02e;
  --grey:#5a5a5a;
  --grey-light:#9a9a9a;
}
*{box-sizing:border-box;margin:0;padding:0}
html,body{width:1200px;height:900px;overflow:hidden}
body{background:var(--stage);font-family:"Montserrat",sans-serif;color:var(--ink);position:relative}

.panel{position:absolute;top:60px;height:780px;overflow:hidden}

/* Cover */
.cover{left:40px;width:360px;background:var(--black);color:var(--paper)}
.cover-flame-top{position:absolute;right:-40px;top:-20px;width:170px;height:330px;
  background:radial-gradient(ellipse at 70% 40%,var(--flame-hot) 0%,var(--orange) 35%,var(--orange-deep) 55%,transparent 72%)}
.cover-flame-bottom{position:absolute;left:-30px;right:-30px;bottom:-40px;height:230px;
  background:radial-gradient(ellipse at 50% 100%,var(--flame-hot) 0%,var(--orange) 30%,var(--orange-deep) 50%,transparent 70%)}
.cover-brand{position:absolute;left:34px;top:80px}
.cover-brand .name{font-size:22px;font-weight:600;letter-spacing:1px}
.cover-brand .tag{font-size:10px;color:var(--orange);letter-spacing:1px;margin-top:4px;text-transform:uppercase}
.cover-title{position:absolute;left:34px;right:40px;top:190px;font-size:52px;font-weight:800;line-height:1.02;letter-spacing:-1px;text-align:center}
.cover-rule{position:absolute;left:140px;top:470px;width:80px;height:2px;background:var(--paper)}
.cover-note{position:absolute;left:34px;right:34px;top:490px;font-size:11px;line-height:1.55;text-align:center;color:#dcdcdc}
.cover-mark{position:absolute;left:0;right:0;top:600px;display:flex;align-items:center;justify-content:center;gap:8px;font-size:15px;font-weight:700;letter-spacing:2px}
.cover-mark .dot{width:14px;height:14px;border-radius:50%;background:var(--paper)}

/* Inner panels */
.inner{width:380px;background:var(--paper);padding:70px 38px 0}
.inner-left{left:420px}
.inner-right{left:800px;background:var(--paper-shade)}
.inner-flame{position:absolute;left:-20px;top:0;width:120px;height:130px;
  background:linear-gradient(160deg,var(--black) 0%,var(--orange-deep) 40%,var(--flame-hot) 80%);
  clip-path:polygon(0 0,100% 0,50% 100%)}

.heading{font-size:22px;font-weight:700;line-height:1.25;text-align:center}
.heading-rule{width:190px;height:2px;background:var(--orange);margin:18px auto 26px}
.subhead{font-size:17px;font-weight:700;text-align:center;margin-bottom:12px}
.body-text{font-size:11px;line-height:1.6;color:var(--grey);text-align:center}

.steps{list-style:none;margin-top:30px}
.step{display:flex;gap:16px;margin-bottom:26px}
.step-num{flex:none;width:32px;height:32px;border-radius:50%;background:var(--orange);color:var(--paper);
  font-size:15px;font-weight:700;display:flex;align-items:center;justify-content:center}
.step-title{font-size:13px;font-weight:700;line-height:1.3;margin-bottom:6px}
.step-text{font-size:11px;line-height:1.55;color:var(--grey)}
.step-text strong{display:block;color:var(--ink);font-size:12px;margin-top:2px}

.cta{display:block;width:200px;margin:26px auto 0;padding:14px 0;border-radius:24px;background:var(--orange);
  color:var(--paper);font-size:13px;font-weight:700;text-align:center}
.footnote{font-size:10px;color:var(--grey);text-align:center;margin-top:22px;line-height:1.5}
.footnote strong{color:var(--ink)}

.set-heading{font-size:24px;font-weight:800;line-height:1.2;text-align:center;margin-top:30px}
.set-sub{font-size:10px;color:var(--grey);text-align:center;margin-top:8px}
.set-box{position:relative;margin:34px 0 0 20px;background:var(--orange);border-radius:14px;padding:24px 16px;text-align:center;color:var(--paper)}
.set-box .badge{position:absolute;left:-22px;top:-20px;width:34px;height:34px;border-radius:50%;background:var(--orange);
  border:3px solid var(--paper-shade);font-weight:700;font-size:15px;display:flex;align-items:center;justify-content:center}
.set-box .big{font-size:30px;font-weight:800;line-height:1.1}
.set-box .small{font-size:10px;margin-top:8px;opacity:.9}
.inner-right .subhead{margin-top:30px}
.inner-right .steps{margin-top:18px}
.inner-right .step{margin-bottom:18px}
</style>
</head>
<body>

<section class="panel cover">
  <div class="cover-flame-top" role="img" aria-label="Flame artwork rising along the right edge"></div>
  <div class="cover-flame-bottom" role="img" aria-label="Flame artwork along the bottom edge"></div>
  <div class="cover-brand">
    <div class="name">VELTO CHURCH</div>
    <div class="tag">A place to belong</div>
  </div>
  <h1 class="cover-title">Are you a Recurring Donor yet?</h1>
  <div class="cover-rule"></div>
  <p class="cover-note">Give once, set it up, and keep blessing our church family every single month through the give platform.</p>
  <div class="cover-mark"><span class="dot"></span>VELTO</div>
</section>

<section class="panel inner inner-left">
  <h2 class="heading">Partner with Velto in Building to the Kingdom</h2>
  <div class="heading-rule"></div>
  <h3 class="subhead">Our Invitation</h3>
  <p class="body-text">Recurring giving helps us plan ahead, serve our city and grow ministries that change lives. Set it up once in a few easy steps.</p>
  <ol class="steps">
    <li class="step"><span class="step-num">1</span>
      <div><div class="step-title">Access the Give Platform Online</div>
      <p class="step-text">Open the give page on our website or app and sign in with your account.</p></div></li>
    <li class="step"><span class="step-num">2</span>
      <div><div class="step-title">Enter Your Recurring Details</div>
      <p class="step-text">Choose an amount, pick the fund and select how often you want to give.</p></div></li>
  </ol>
  <span class="cta">Start Giving</span>
  <p class="footnote">Thank you for your faithful support</p>
</section>

<section class="panel inner inner-right">
  <div class="inner-flame" role="img" aria-label="Flame artwork in a triangular corner"></div>
  <h2 class="set-heading">That's it—<br>You're all Set!</h2>
  <p class="set-sub">Your gift now goes out automatically</p>
  <div class="set-box">
    <span class="badge">3</span>
    <div class="big">YOU'RE<br>ALL SET</div>
    <p class="small">No more reminders needed each week</p>
  </div>
  <h3 class="subhead">Instruction</h3>
  <ol class="steps">
    <li class="step"><span class="step-num">4</span>
      <p class="step-text">Review your gift and confirm the schedule <strong>Save Changes</strong></p></li>
    <li class="step"><span class="step-num">5</span>
      <p class="step-text">Look for a confirmation email in your inbox <strong>Check Email</strong></p></li>
    <li class="step"><span class="step-num">6</span>
      <p class="step-text">You can edit or pause your gift at any time</p></li>
  </ol>
  <span class="cta">Give Now</span>
  <p class="footnote"><strong>Questions about giving? Visit our welcome desk</strong><br>We are happy to help you</p>
</section>

</body>
</html>
```